Corvanth Veylor - Advanced Skincare and undetectable Makeup for Men

We are in need of a professional webpage for our company Corvanth Veylor. We help every man feel his best by looking his best. Inspired by the myth of Corvanth, we offer makeup and skincare products along with education upon their use. Our mission is to celebrate masculinity in all of its forms, regardless of age, race, sexual orientation, or assigned gender at birth.

The webpage would serve as our online store, as a place where our clients can learn about our brand, view our "How-to" video tutorials, and get product information. An online blog will also be hosted in order to keep clients up to date with news, updates, media mentions, etc.

The color schemes that we use are mostly Black and Gold, with Red accents. please keep in mind that this is a men's cosmetics line, and therefore should read powerful, sexy, confident and bold - all with a high end look and feel.

Think along the lines of brands like Lem Brisko, QDV, Belluti, etc.

our logo is included in the files attached. images and copy will be added in at a later time; hence, general images that fit the feel and filler text is encouraged.

The products to be sold include:
a face cleanser in a pump dispenser bottle (1 size)
a mask in a round jar container (1 size)
a moisturizer in a pump container 1 size)
a concealer in a click pen with a brush applicator (3 shades)
a liquid liner pen (4 shades)
a contouring palette (2 shade options)
a setting spray (single option)

Target Market(s)

Millennial Men

Industry/Entity Type

Beauty

Number of Pages Required

5+ page

Font styles to use
Serif

Colors
ec1f27
000000
faa54b

Requirements
Must have
• ur essential requirements are:
• 1) a stunning and engaging landing page that truly captures the ideals of sexuality, boldness and confidence.
• 2) an interactive and engaging online store that is easy to update / add product / information to.
• 3) Product pages supporting various toggling images of the product, a shade selection option, ingredient information, usage instructions, pricing, and a link to a "how to video" unique to each individual product.
• 4) dedicated space where all of the tutorials can be organized together
• 5) an organized Blog section, that would include a segment for a Q&A section for us to update as the brand grows, ongoing contests (that would be easily hidden if there are no contests running at the moment) as well as general news and updates segment.
• 6) an "about us" page, where our customers are able to learn about our story, inspirations, humanitarian efforts and philosophies in product contents and purity.
• 7) a contact us page, which would include social media links, contact email and telephone number as well as physical address to be updated upon launch.
• 8) discrete privacy policy, terms of use, and return policy links available at the bottom of every page
Nice to have
• 1) A posting forum where clients could post their looks using our products, or maybe a live stream of our Pictoval account.
• 2) a member sign in page so that we can collect and store customer information for faster check out, keep track of purchases attached to their email address (future loyalty program plans) and maintain an email database for email notifications and the such.

```html
<!DOCTYPE html>
<html lang="en">
<head>
<meta charset="utf-8">
<title>Face Mask – Corvanth Veylor</title>
<link href="https://fonts.googleapis.com/css2?family=Montserrat:wght@400;500;600;700&family=Cinzel:wght@500&display=swap" rel="stylesheet">
<style>
:root{
  --bg:#000;
  --ink:#fff;
  --muted:#b9b9b9;
  --gold:#b8863b;
  --gold-deep:#a8792f;
  --panel:#fff;
  --field-line:#d6d6d6;
  --placeholder:#8a8a8a;
  --swatch-orange:#ff7a00;
  --swatch-cyan:#00e5ff;
  --swatch-green:#1ee81e;
  --btn:#2b2b2b;
}
*{box-sizing:border-box;margin:0;padding:0}
html,body{width:1200px;height:1100px;overflow:hidden;background:var(--bg)}
body{position:relative;font-family:"Montserrat",sans-serif;color:var(--ink)}
.abs{position:absolute}
a{color:inherit;text-decoration:none}

.brand{font-family:"Cinzel",serif;color:var(--gold);letter-spacing:1px;font-size:7px;white-space:nowrap;width:96px;text-align:center}
.brand-header{left:58px;top:58px}
.brand-footer{left:247px;top:752px}

.main-nav{left:180px;top:39px;display:flex;font-size:9px;font-weight:600;color:var(--muted);letter-spacing:.2px}
.main-nav a{margin-right:25px}
.main-nav .chev{margin-left:6px}

.cart{left:763px;top:38px;font-size:9px;font-weight:600;color:var(--muted);display:flex;align-items:center;gap:3px}
.account{left:837px;top:28px;width:31px;height:31px;border:1px solid var(--muted);border-radius:50%;display:flex;align-items:center;justify-content:center}
.search{left:894px;top:38px;font-size:9px;color:var(--muted);display:flex;align-items:center;gap:6px}
.langs{left:1092px;top:41px;display:flex;gap:9px}
.langs span{width:10px;height:7px;display:block}

.product-shot{left:278px;top:144px;width:188px;height:312px;border-radius:2px;
  background:linear-gradient(90deg,#5fae18 0%,#7cc520 28%,#e9ecef 55%,#fafafa 72%,#9fd14a 100%)}
.thumb{top:505px;border-radius:2px}
.thumb-a{left:285px;width:55px;height:52px;background:radial-gradient(circle at 60% 40%,#f0a020,#3a2a14 60%,#000 80%)}
.thumb-b{left:377px;width:40px;height:62px;background:linear-gradient(90deg,#6cbf1c,#eeeeee 60%,#8fcd3a)}

.back-link{left:577px;top:134px;font-size:9.5px;font-weight:500;color:var(--muted)}
.title{left:577px;top:162px;font-size:27px;font-weight:500}
.price{left:582px;top:204px;font-size:11.5px;font-weight:600;word-spacing:6px}
.description{left:577px;top:236px;width:372px;font-size:10.5px;font-weight:500;line-height:16.4px}
.label{font-size:7px;font-weight:700;letter-spacing:.2px}
.colour-label{left:577px;top:382px}
.swatches{left:629px;top:380px;display:flex;gap:13px}
.swatches span{width:12px;height:12px;border-radius:50%}
.included-label{left:577px;top:406px;font-size:6px}
.included{left:595px;top:422px;list-style:none;font-size:5.3px;font-weight:600;color:#ddd;line-height:14.4px}
.included li::before{content:"• "}
.add-cart{left:577px;top:497px;width:89px;height:26px;background:var(--btn);border-radius:2px;font-size:8.5px;letter-spacing:1.6px;font-weight:500;display:flex;align-items:center;justify-content:center}

.divider{left:0;top:629px;width:1200px;height:1px;background:var(--gold-deep)}

.footer-about{left:247px;top:771px;width:202px;font-size:10.4px;font-weight:500;line-height:16.4px}
.footer-col{top:704px;font-size:10.5px;font-weight:500}
.footer-col h4{font-weight:500;font-size:10.5px;margin-bottom:8px}
.footer-col li{list-style:none;margin-left:9px;line-height:22.6px}
.col-resources{left:486px}
.col-company{left:726px}

.friends{left:0;width:1200px;top:986px;text-align:center;font-size:16px;font-weight:400}
.socials{left:0;width:1200px;top:1019px;display:flex;justify-content:center;gap:26px}
.social{display:flex;align-items:center;gap:6px;font-size:9px;font-weight:500}
.social i{width:30px;height:30px;border:1px solid #888;border-radius:50%;display:block}
.rule{left:241px;top:1068px;width:719px;height:1px;background:#333}
.made{left:487px;top:1093px;font-size:7px;font-weight:600;color:#ddd}

.contact-widget{left:957px;top:575px;width:221px;height:342px;background:var(--panel);color:#222;border-radius:2px}
.widget-head{height:34px;background:var(--gold);display:flex;align-items:center;padding-left:35px;font-size:8.5px;font-weight:600;color:#fff;position:relative}
.widget-head .toggle{position:absolute;right:0;top:0;width:32px;height:34px;background:var(--gold-deep);display:flex;align-items:center;justify-content:center}
.widget-head .chat{position:absolute;left:8px;top:10px}
.widget-body{padding:13px 10px 0}
.widget-body h3{font-size:9.5px;font-weight:700;margin-bottom:12px}
.widget-body p{font-size:9.5px;font-weight:500;margin-bottom:12px}
.field{height:32px;border:1px solid var(--field-line);margin-bottom:6px;display:flex;align-items:center;font-size:8px;color:var(--placeholder)}
.field svg{margin:0 14px 0 11px}
.field.message{height:80px;align-items:flex-start;padding:8px;font-size:8px}
.send{height:32px;background:#000;color:#fff;font-size:8.5px;font-weight:600;display:flex;align-items:center;justify-content:center}
</style>
</head>
<body>

<header>
  <div class="abs brand brand-header">Corvanth Veylor</div>
  <nav class="abs main-nav">
    <a href="#">HOME</a>
    <a href="#">PRODUCTS<span class="chev">›</span></a>
    <a href="#">ABOUT US</a>
    <a href="#">CONTACT</a>
    <a href="#">BLOG</a>
  </nav>
  <div class="abs cart">
    <svg width="14" height="12" viewBox="0 0 14 12" fill="none" stroke="#b9b9b9" stroke-width="1"><path d="M0.5 1h2l1.6 7h7.4l1.5-5H3.2"/><circle cx="5" cy="10.5" r="1"/><circle cx="10.5" cy="10.5" r="1"/></svg>
    CART (0)
  </div>
  <div class="abs account">
    <svg width="11" height="12" viewBox="0 0 11 12" fill="none" stroke="#ccc" stroke-width="1"><circle cx="5.5" cy="3.5" r="2.8"/><path d="M0.8 11.5c0-2.8 2-4.3 4.7-4.3s4.7 1.5 4.7 4.3"/></svg>
  </div>
  <div class="abs search">
    <svg width="11" height="11" viewBox="0 0 11 11" fill="none" stroke="#b9b9b9" stroke-width="1.1"><circle cx="4.6" cy="4.6" r="3.8"/><path d="M7.4 7.4L10.5 10.5"/></svg>
    Search Corvanth Veylor
  </div>
  <div class="abs langs">
    <span style="background:linear-gradient(#b22 0 50%,#eee 50%)"></span>
    <span style="background:linear-gradient(90deg,#1a7a3a 33%,#eee 33% 66%,#c22 66%)"></span>
    <span style="background:linear-gradient(#c22,#c22) center/100% 2px no-repeat,linear-gradient(#c22,#c22) center/2px 100% no-repeat,#1c3a8a"></span>
  </div>
</header>

<main>
  <div class="abs product-shot" role="img" aria-label="Product photo: green box and white tube of face mask"></div>
  <div class="abs thumb thumb-a" role="img" aria-label="Thumbnail: gold compact product"></div>
  <div class="abs thumb thumb-b" role="img" aria-label="Thumbnail: green box and tube"></div>

  <a class="abs back-link" href="#">« BACK TO FACE CLEANSER</a>
  <h1 class="abs title">Face Mask</h1>
  <div class="abs price">$ 1199.99</div>
  <p class="abs description">Fusce eros sapien, dapibus in eleifend ac, faucibus et justo. Aenean ultrices nisi ipsum, at tempus dui lobortis ac. Nulla quis neque bibendum, interdum mauris et, dapibus justo. In et ligula euismod, ultricies mauris eu, ultrices velit. Vestibulum molestie accumsan quam, mattis commodo diam blandit vel. Nulla viverra libero ut consequat viverra. Sed pellentesque nec erat a elementum. Nulla dolor nibh, efficitur quis augue non, finibus porttitor eros. Cras volutpat blandit pellentesque.</p>

  <div class="abs label colour-label">COLOUR</div>
  <div class="abs swatches">
    <span style="background:var(--swatch-orange)"></span>
    <span style="background:var(--swatch-cyan)"></span>
    <span style="background:var(--swatch-green)"></span>
  </div>
  <div class="abs label included-label">WHATS INCLUDED</div>
  <ul class="abs included">
    <li>5 STANDARD CHIP BRUSHES (SIZES 2 1/2", 4")</li>
    <li>2 GOLDEN SYNTHETIC SHADER BRUSHES (SIZES 4, 8)</li>
    <li>2 WHITE SYNTHETIC SHADER BRUSHES (SIZES 4, 6)</li>
    <li>1 WHITE SYNTHETIC LINER BRUSH (SIZE 1)</li>
  </ul>
  <a class="abs add-cart" href="#">ADD TO CART</a>
</main>

<div class="abs divider"></div>

<footer>
  <div class="abs brand brand-footer">Corvanth Veylor</div>
  <p class="abs footer-about">Lorem ipsum dolor sit amet, consectetur adipiscing elit. Suspendisse varius enim in eros elementum tristique. Duis cursus, mi quis viverra ornare, eros dolor interdum nulla, ut commodo diam libero vitae erat. Aenean faucibus nibh et justo cursus id rutrum lorem imperdiet. Nunc ut sem vitae risus tristique posuere.</p>
  <div class="abs footer-col col-resources">
    <h4>Resources</h4>
    <ul><li>Licenses</li><li>Blog</li><li>Discussions</li><li>Products</li><li>Collections</li><li>Help Center</li></ul>
  </div>
  <div class="abs footer-col col-company">
    <h4>Company</h4>
    <ul><li>About</li><li>Brand</li><li>Terms</li><li>Cookie Policy</li><li>Privacy Policy</li><li>Careers</li></ul>
  </div>

  <div class="abs friends">let's be friends</div>
  <div class="abs socials">
    <a class="social" href="#"><i></i>Folkwall</a>
    <a class="social" href="#"><i></i>Chirpline</a>
    <a class="social" href="#"><i></i>Pictoval</a>
  </div>
  <div class="abs rule"></div>
  <div class="abs made">Made With <span style="color:#e22">♥</span></div>
</footer>

<aside class="abs contact-widget">
  <div class="widget-head">
    <svg class="chat" width="15" height="13" viewBox="0 0 15 13" fill="none" stroke="#fff" stroke-width="1"><rect x="0.5" y="0.5" width="10" height="7" rx="1"/><path d="M3 7.5v3l2.5-3M12 3.5h2v7h-2v2l-2.5-2H5.5"/></svg>
    Contact Us
    <span class="toggle"><svg width="10" height="6" viewBox="0 0 10 6" fill="none" stroke="#fff" stroke-width="1.1"><path d="M1 5.5L5 1.5l4 4"/></svg></span>
  </div>
  <div class="widget-body">
    <h3>How Can We Help You?</h3>
    <p>Please, leave us your message.</p>
    <div class="field"><svg width="11" height="12" viewBox="0 0 11 12" fill="none" stroke="#333" stroke-width="1"><circle cx="5.5" cy="3.5" r="2.8"/><path d="M0.8 11.5c0-2.8 2-4.3 4.7-4.3s4.7 1.5 4.7 4.3"/></svg>Enter your name</div>
    <div class="field"><svg width="13" height="10" viewBox="0 0 13 10" fill="none" stroke="#333" stroke-width="1"><rect x="0.5" y="0.5" width="12" height="9"/><path d="M0.5 0.5l6 5 6-5"/></svg>Enter your email</div>
    <div class="field"><svg width="12" height="12" viewBox="0 0 12 12" fill="none" stroke="#333" stroke-width="1"><path d="M2.5 0.8l2 2.4-1.2 1.4c.8 1.7 2.2 3 3.9 3.9l1.4-1.2 2.4 2-1.2 1.9C5.5 11 1 6.5.8 2z"/></svg>Enter your phone</div>
    <div class="field message">How can we help you?</div>
    <a class="send" href="#">Send Message</a>
  </div>
</aside>

</body>
</html>
```